Coastline Premier Retreats Business Card Design

Design a business card for Coastline Premier Retreats. Look at the website for colors and reference. Card should have logo, name, title, office number, mobile number, email, URL and a tagline like, "Luxury Hotel & Resort Email Marketing" (This might change).

https://www.coastlinepremierretreats.example

The rest I will leave up to your imagination.

Contact Information for Business Card

Logo, name, title, office number, mobile number, email, URL and a tagline like, "Luxury Hotel & Resort Email Marketing" (This might change).

```html
<!DOCTYPE html>
<html lang="en">
<head>
<meta charset="utf-8">
<title>Coastline Premier Retreats – Business Card</title>
<link href="https://fonts.googleapis.com/css2?family=Lato:wght@400;700&family=Montserrat:wght@700&family=Dancing+Script:wght@500&display=swap" rel="stylesheet">
<style>
  :root {
    --backdrop: #3b3b3d;
    --card-dark: #1d1d1f;
    --card-light: #ffffff;
    --accent: #f47216;
    --ink: #111111;
    --text-light: #f2f2f2;
    --text-muted: #cfcfcf;
  }
  * { box-sizing: border-box; margin: 0; padding: 0; }
  html, body { width: 1200px; height: 689px; overflow: hidden; }
  body {
    background: var(--backdrop);
    font-family: "Lato", Arial, sans-serif;
    position: relative;
  }
  .card {
    position: absolute;
    top: 196px;
    width: 520px;
    height: 297px;
    overflow: hidden;
    box-shadow: 0 10px 30px rgba(0,0,0,.35);
  }
  .card--front { left: 60px; background: var(--card-dark); }
  .card--back  { left: 620px; background: var(--card-light); }

  .brand {
    font-family: "Montserrat", Arial, sans-serif;
    font-weight: 700;
    text-transform: uppercase;
    letter-spacing: 1px;
    display: flex;
    align-items: center;
    gap: 10px;
  }
  .brand__mark { width: 14px; height: 14px; background: var(--accent); flex: none; }
  .card--front .brand {
    position: absolute; left: 32px; top: 40px;
    color: var(--text-light); font-size: 20px; line-height: 1.15;
  }

  .person { position: absolute; left: 32px; top: 186px; }
  .person__name {
    font-weight: 700; font-size: 21px; color: var(--accent);
    text-transform: uppercase; letter-spacing: .5px;
  }
  .person__title { font-size: 14px; color: var(--text-light); margin-top: 3px; }

  .contact {
    position: absolute; left: 262px; top: 118px;
    list-style: none; font-size: 11.5px; color: var(--text-muted);
  }
  .contact li { display: flex; align-items: flex-start; gap: 8px; margin-bottom: 6px; line-height: 1.35; }
  .contact svg { width: 11px; height: 11px; flex: none; margin-top: 2px; fill: var(--accent); }

  .band { position: absolute; bottom: 0; height: 9px; }
  .band--accent { left: 0; width: 62%; background: var(--accent); }
  .band--light  { right: 0; width: 38%; background: var(--card-light); bottom: 22px; height: 7px; }

  .card--back .brand {
    position: absolute; left: 0; right: 0; top: 112px;
    justify-content: center; color: var(--ink); font-size: 24px;
  }
  .tagline {
    position: absolute; left: 0; right: 0; top: 176px;
    text-align: center; font-family: "Dancing Script", cursive;
    font-size: 21px; color: var(--accent);
  }
</style>
</head>
<body>
  <section class="card card--front">
    <div class="brand"><span class="brand__mark"></span><span>Coastline Premier<br>Retreats</span></div>
    <div class="person">
      <p class="person__name">Daniel Reyes</p>
      <p class="person__title">Founder &amp; CEO</p>
    </div>
    <ul class="contact">
      <li><svg viewBox="0 0 24 24"><path d="M12 2a7 7 0 0 0-7 7c0 5 7 13 7 13s7-8 7-13a7 7 0 0 0-7-7zm0 9.5A2.5 2.5 0 1 1 12 6.5a2.5 2.5 0 0 1 0 5z"/></svg><span>4470 Harbor View Lane<br>Mystic, CT 06355</span></li>
      <li><svg viewBox="0 0 24 24"><path d="M6.6 10.8a15 15 0 0 0 6.6 6.6l2.2-2.2c.3-.3.7-.4 1-.2 1.1.4 2.3.6 3.6.6.6 0 1 .4 1 1V20c0 .6-.4 1-1 1A17 17 0 0 1 3 4c0-.6.4-1 1-1h3.5c.6 0 1 .4 1 1 0 1.3.2 2.5.6 3.6.1.3 0 .7-.2 1z"/></svg><span>(555) 014-2290</span></li>
      <li><svg viewBox="0 0 24 24"><path d="M7 1h10a2 2 0 0 1 2 2v18a2 2 0 0 1-2 2H7a2 2 0 0 1-2-2V3a2 2 0 0 1 2-2zm0 3v14h10V4z"/></svg><span>(555) 014-7731</span></li>
      <li><svg viewBox="0 0 24 24"><path d="M2 5h20v14H2zm2 2v.5l8 5 8-5V7z"/></svg><span>info@coastlinepremierretreats.example</span></li>
      <li><svg viewBox="0 0 24 24"><circle cx="12" cy="12" r="10"/></svg><span>coastlinepremierretreats.example</span></li>
    </ul>
    <div class="band band--accent"></div>
    <div class="band band--light"></div>
  </section>

  <section class="card card--back">
    <div class="brand"><span class="brand__mark"></span><span>Coastline Premier Retreats</span></div>
    <p class="tagline">Luxury Hotel &amp; Resort Email Marketing</p>
  </section>
</body>
</html>
```